Web Design Project

We need a web design company for a company based in London. We are an online minicab booking service that produces real time quotes on cab journey for consumers. Our colours are currently red and yellow, but do not need to stay that way; it's open to interpretation. Please avoid yellow and black as a colour combination. Our current site is: www.rovelink.co.uk We are looking for a new site to be user-friendly and easy to use, but more polished and professional looking, without using it usability and simplicity. We need to keep the booking capability on each page and it needs to draw in the user's eye. We need a site that is reliable and easy to use, but also fun.

Main objective: keep it simple, like it is now, but polish it up some. Also, we need to be able to add more content to it. And, we will also be adding a login capability for return users.

Target Market(s)

Internet-savvy people aged 18 and older.

Industry/Entity Type

It Company

Requirements
Must have
• Must have the booking widget. However, it doesn't have to be as large as it is now. We are actually thinking to split it over two pages. We will add a few options to the booking widget, such as another via option. The booking widget must be the most noticeable feature on the page. Sans serif font, please.
Should not have
• Should not be too busy and distracting. Please do not use any images of traditional taxis, ie. black cabs from London or yellow cabs from NYC. Our cars do not resemble these and our business cannot be associated with these images.

```html
<!DOCTYPE html>
<html lang="en">
<head>
<meta charset="utf-8">
<title>Rovelink – Order your cab online</title>
<link href="https://fonts.googleapis.com/css2?family=Arimo:wght@400;700&display=swap" rel="stylesheet">
<style>
:root{
  --sky-top:#8fd0f4;
  --sky-mid:#d9eefa;
  --band:#a8dcf3;
  --navy:#1b5e96;
  --red:#c0141a;
  --ink:#333333;
  --muted:#666666;
  --panel:#e6f5fc;
  --panel-line:#57b8e6;
  --field-line:#b9dff0;
  --btn-top:#fde08a;
  --btn-bot:#f3a92b;
  --story-bg:#fdf8f1;
  --story-line:#e5d7c4;
  --green:#22a02a;
  --rule:#cccccc;
}
*{box-sizing:border-box;margin:0;padding:0}
html,body{width:1200px;height:1080px;overflow:hidden;background:#fff}
body{font-family:"Arimo",Arial,sans-serif;color:var(--ink);position:relative}
.abs{position:absolute}

/* header */
.site-header{left:0;top:0;width:1200px;height:220px;background:linear-gradient(#9ad4f5 0%,#d6edfa 45%,#ffffff 100%)}
.brand{left:34px;top:52px;display:flex;align-items:center;gap:16px}
.brand-mark{width:64px;height:64px;border-radius:50%;background:var(--red)}
.brand-name{font-size:72px;font-weight:700;color:var(--red);letter-spacing:-1px}
.tagline{left:46px;top:172px;font-size:29px;color:var(--navy)}
.social{top:22px;display:flex;gap:8px;left:1054px}
.social span{width:28px;height:26px;border-radius:3px}
.social .s1{background:#d34836}.social .s2{background:#3b5998}.social .s3{background:#55acee}
.booking-line{left:893px;top:78px;display:flex;align-items:center;gap:16px;font-size:18px;color:var(--navy)}
.driver-link{left:960px;top:130px;width:180px;text-align:center;font-size:14px;color:var(--green);line-height:1.25}
.driver-link svg{display:block;margin:0 auto 6px}

/* nav */
.main-nav{left:0;top:220px;width:1200px;height:48px;background:linear-gradient(#e9f6fd,#a6dcf3)}
.main-nav ul{list-style:none;display:flex;position:absolute;right:54px;top:14px;font-size:17px;color:var(--navy)}
.main-nav li{padding:0 25px;border-left:1px solid var(--navy);line-height:18px}
.main-nav li:first-child{border-left:0}

/* headings */
.col-title{font-size:22px;font-weight:400;color:var(--red)}

/* booking widget */
.booking{left:26px;top:320px;width:370px;height:390px;background:linear-gradient(#f6fcff,var(--panel));border:1px solid var(--panel-line);border-radius:8px}
.field-label{font-size:17px;color:var(--red)}
.field{height:31px;background:#fff;border:1px solid var(--field-line);font-size:13px;font-style:italic;color:var(--muted);padding:8px 10px}
.btn{height:29px;border:1px solid #e39a26;border-radius:4px;background:linear-gradient(var(--btn-top),var(--btn-bot));color:var(--navy);font-size:16px;text-align:center;line-height:27px}
.select{height:22px;background:#fff;border:1px solid #cfcfcf;font-size:14px;padding:2px 6px;display:flex;justify-content:space-between;align-items:center}
.select i{width:18px;height:18px;border:1px solid #888;background:#eee;position:relative}
.select i:after{content:"";position:absolute;left:4px;top:6px;border:4px solid transparent;border-top:6px solid #222}
.check{width:14px;height:14px;border:1px solid #888;background:#f4f4f4}
.small{font-size:14px;color:var(--muted)}

/* info form */
.info{left:418px;top:322px;width:291px;height:386px;background:#fff;border:1px solid #e4e4e4;border-top:2px solid #d8d8d8;border-bottom:2px solid #d8d8d8}

/* story */
.story{left:728px;top:325px;width:416px;height:249px;background:var(--story-bg);border:1px solid var(--story-line);box-shadow:0 2px 3px rgba(0,0,0,.1);padding:14px 15px;font-size:14px;line-height:16.6px;color:var(--muted);text-align:justify}
.avatar{left:754px;top:607px;width:38px;height:44px;border-radius:19px 19px 6px 6px;background:linear-gradient(#f0c9a0 45%,#3a9ad6 45%)}
.author{left:796px;top:637px;font-size:13px;color:#222}

.rule{left:24px;top:739px;width:1129px;height:1px;background:var(--rule)}

/* why */
.why-title{left:41px;top:750px;font-size:21px;font-weight:400;color:var(--navy)}
.point{left:42px;width:660px}
.point h3{font-size:20px;font-weight:400;color:var(--red);display:inline-block;border-bottom:2px solid var(--red);padding-bottom:1px;margin-bottom:2px;line-height:22px}
.point p{font-size:16.5px;line-height:21px}
.easy-title{left:745px;top:761px;font-size:22px;font-weight:400;color:var(--navy)}
.easy-sub{left:749px;top:796px;font-size:14px;color:var(--muted)}
.steps{left:749px;top:838px;font-size:16.5px;line-height:21.5px;list-style:none}

.site-footer{left:0;top:1034px;width:1200px;height:46px;background:linear-gradient(#e8f6fd,#a8dcf3);font-size:13px;color:#444;text-align:right;padding:16px 30px 0 0}
</style>
</head>
<body>

<header class="site-header abs">
  <div class="brand abs"><span class="brand-mark"></span><span class="brand-name">Rovelink</span></div>
  <div class="tagline abs">Order your cab online</div>
  <div class="social abs"><span class="s1"></span><span class="s2"></span><span class="s3"></span></div>
  <div class="booking-line abs">
    <svg width="44" height="50" viewBox="0 0 44 50"><rect x="2" y="1" width="40" height="48" rx="5" fill="#3fa335"/><path d="M14 13c2-1 4 3 4 5s-2 2-1 4 4 5 6 6 2-1 4-1 6 2 5 4-3 4-6 3-9-5-12-9-4-10 0-12z" fill="#fff"/></svg>
    <span>020 7946 0321: Booking Line</span>
  </div>
  <div class="driver-link abs">
    <svg width="44" height="36" viewBox="0 0 44 36"><ellipse cx="17" cy="14" rx="14" ry="11" fill="#2c8fd4"/><ellipse cx="28" cy="22" rx="13" ry="10" fill="#6cc04a"/></svg>
    Are you a taxi driver<br>or a company?
  </div>
</header>

<nav class="main-nav abs">
  <ul><li>Home</li><li>Rovelink Miles</li><li>Join Us</li><li>About Us</li><li>Contact</li></ul>
</nav>

<h2 class="col-title abs" style="left:32px;top:288px">Book a cab</h2>
<h2 class="col-title abs" style="left:426px;top:288px">your information</h2>
<h2 class="col-title abs" style="left:744px;top:287px">The best stories from our community</h2>

<section class="booking abs">
  <div class="field-label abs" style="left:34px;top:22px">Pick me up from:</div>
  <div class="field abs" style="left:30px;top:46px;width:252px">e.g pick up address or post code</div>
  <div class="btn abs" style="left:292px;top:48px;width:66px">Find</div>
  <div class="field-label abs" style="left:33px;top:95px">Drop me at:</div>
  <div class="field abs" style="left:30px;top:119px;width:252px">e.g drop address or post code</div>
  <div class="btn abs" style="left:292px;top:121px;width:66px">Find</div>
  <div class="field-label abs" style="left:29px;top:168px">Pick up date and time</div>
  <div class="field abs" style="left:30px;top:191px;width:252px;color:#333">06-Apr-2012 @ 12.00</div>
  <svg class="abs" style="left:291px;top:190px" width="32" height="32" viewBox="0 0 32 32"><rect x="1" y="3" width="30" height="28" fill="#fff" stroke="#8aa8c8"/><rect x="1" y="3" width="30" height="6" fill="#5c8fd0"/><path d="M1 15h30M1 21h30M1 27h30M8 9v22M15 9v22M22 9v22" stroke="#b8c8dc"/></svg>
  <div class="small abs" style="left:26px;top:233px">Just pick me up in</div>
  <div class="select abs" style="left:169px;top:232px;width:115px"><span>----</span><i></i></div>
  <div class="field-label abs" style="left:22px;top:277px">Passengers:</div>
  <div class="select abs" style="left:122px;top:277px;width:52px"><span>1</span><i></i></div>
  <div class="small abs" style="left:183px;top:280px">Adults</div>
  <div class="select abs" style="left:228px;top:277px;width:53px"><span>0</span><i></i></div>
  <div class="small abs" style="left:288px;top:283px">Bags</div>
  <div class="check abs" style="left:22px;top:324px"></div>
  <div class="field-label abs" style="left:48px;top:323px">Return Journey:</div>
  <div class="check abs" style="left:22px;top:357px"></div>
  <div class="field-label abs" style="left:49px;top:356px">Extras:</div>
</section>

<section class="info abs">
  <div class="field-label abs" style="left:16px;top:38px">Mobile Number:</div>
  <div class="field abs" style="left:10px;top:75px;width:253px">your mobile number</div>
  <div class="field-label abs" style="left:18px;top:116px">Name:</div>
  <div class="field abs" style="left:10px;top:136px;width:253px">your name</div>
  <div class="field-label abs" style="left:15px;top:177px">Email:</div>
  <div class="field abs" style="left:10px;top:198px;width:253px">your email address</div>
  <div class="field-label abs" style="left:15px;top:237px">Comments:</div>
  <div class="field abs" style="left:10px;top:257px;width:253px">type any special instruction here</div>
  <div class="btn abs" style="left:197px;top:317px;width:66px">Submit</div>
</section>

<blockquote class="story abs">I recently hit London for a girlie night on the town with my bestie. After a little too much champagne, we had a stupid argument and decided to leave the club early. In the cab on our way home, we didn't say one word to each other. The driver who could sense we were both upset however, had other plans. He randomly started singing The Tidewells' Summer Avenue! My best friend and I were in shock, we looked at each other and couldn't stop laughing! The remainder of the journey consisted of us all belting out Tidewells classics, in between fits of laughter. We were so disappointed when we arrived home as we wanted to continue the fun, we will never forget our singing taxi driver!</blockquote>
<svg class="abs" style="left:784px;top:572px" width="40" height="32" viewBox="0 0 40 32"><path d="M0 0H38L4 30Z" fill="#fdf8f1" stroke="#e5d7c4"/><path d="M0 -1H39" stroke="#fdf8f1" stroke-width="3"/></svg>
<div class="avatar abs" role="img" aria-label="Small user avatar icon"></div>
<div class="author abs">Meera</div>

<div class="rule abs"></div>

<h2 class="why-title abs">Why Rovelink ?</h2>
<div class="point abs" style="top:786px"><h3>Price</h3><p>Rovelink guarantees that you get the best deal for your travel, as you get quotes from several cab companies.</p></div>
<div class="point abs" style="top:873px"><h3>No fees</h3><p>There's absolutely no cost for you to use our service.</p></div>
<div class="point abs" style="top:938px"><h3>Coverage</h3><p>Rovelink has the largest database of licensed minicab operators. You can use Rovelink wherever you are in greater London.</p></div>

<h2 class="easy-title abs">As easy as opening the cab's door</h2>
<div class="easy-sub abs">Its free, dependable and with no obligation</div>
<ol class="steps abs">
  <li>1. Enter your route</li>
  <li>2. Quickly compare taxi fares</li>
  <li>3. Get your travel confirmed on your phone by SMS.</li>
</ol>

<footer class="site-footer abs">rovelink @20-20 Quickstep.com all rights reserved.</footer>

</body>
</html>
```